International business needs business cards

Our company, DRV Ventures Inc. is in the business of supplying a range construction products with particular emphasis on CEMENT. We have developed our own brand - TORVAN SUPPLIES - with which to infiltrate the market. We are launching our brand of cement (TORVAN Type IS Cement) into the Caribbean which is unlike anything this market has ever seen. A monopoly has existed here for the past 60-odd years and the market has now opened to allow the importation of other brands and consumers are anxious and ready for change/improvement. We are very excited to be launching and want to make a great first impression. We will be conducting workshops and seminars (from government level to the hardware store owners) and we want our business card to give us the strong, confident introduction that we need.

Target Market(s)

construction; builders; engineers; home owners

Industry/Entity Type

Construction

Contact Information for Business Card

Marisol Depree
CEO
cell # 1 555 4180736
Ground floor,Lindell Plaza Suite 2734
George Town,Grand Cayman
Cayman Islands,KY1-4823
EMAIL: m.depree@drvventuresinc.example
web site drvventuresinc.example

COMPANY: skype info drv.ventures.example

second card
Yvette Brannock-Depree
CFO
CELL# 1 555 607 3941
George Town,Grand Cayman
Cayman Islands,KY1-4823
EMAIL: y.brannockdepree@drvventuresinc.example
website drvventuresinc.example

Requirements
Must have
• Business cards must display BOTH logos - DRV is the company and TORVAN is the brand.

```html
<!DOCTYPE html>
<html lang="en">
<head>
<meta charset="utf-8">
<title>DRV Ventures Inc. – Business Card</title>
<link rel="stylesheet" href="https://fonts.googleapis.com/css2?family=Open+Sans:wght@400;600;700&display=swap">
<style>
  :root {
    --backdrop: #34302d;
    --card: #131313;
    --card-edge: #1c1c1c;
    --brand-red: #a3161c;
    --name-red: #b0252b;
    --text-light: #e6e6e6;
    --text-muted: #c9c9c9;
    --divider: #6a6a6a;
    --crest-light: #8d8d8d;
    --crest-dark: #2a2a2a;
  }
  * { box-sizing: border-box; margin: 0; padding: 0; }
  html, body {
    width: 1200px; height: 814px; overflow: hidden;
    background: var(--backdrop);
    font-family: "Open Sans", Arial, sans-serif;
  }
  .stage {
    position: relative; width: 1200px; height: 814px;
    display: flex; align-items: center; justify-content: center; gap: 40px;
  }
  .card {
    position: relative; width: 540px; height: 309px;
    background: var(--card);
    border: 1px solid var(--card-edge);
    box-shadow: 0 10px 28px rgba(0,0,0,.45);
  }

  /* Front */
  .logo {
    position: absolute; left: 26px; top: 104px;
    display: flex; align-items: center; gap: 10px;
  }
  .logo-square { width: 40px; height: 40px; background: var(--brand-red); }
  .logo-name {
    color: var(--text-light); font-weight: 700; font-size: 17px; letter-spacing: .2px;
    white-space: nowrap;
  }
  .crest-small {
    position: absolute; left: 62px; top: 168px; width: 110px; height: 96px;
    border-radius: 46% 46% 40% 40%;
    background: radial-gradient(ellipse at 50% 40%, #5a5a5a 0%, #3a3a3a 45%, var(--card) 80%);
  }
  .divider {
    position: absolute; left: 236px; top: 34px; width: 1px; height: 240px;
    background: linear-gradient(to bottom, transparent, var(--divider) 20%, var(--divider) 80%, transparent);
  }
  .contact {
    position: absolute; left: 252px; top: 48px; color: var(--text-muted);
    font-size: 13.5px; line-height: 19px;
  }
  .contact-name { color: var(--name-red); font-weight: 600; font-size: 18px; line-height: 24px; }
  .contact-title { margin-bottom: 6px; }
  .contact-lines { margin-bottom: 4px; }
  .contact-row { display: flex; align-items: center; gap: 7px; }
  .contact-row svg { width: 12px; height: 12px; flex: none; }

  /* Back */
  .crest-large {
    position: absolute; left: 50%; top: 62px; width: 190px; height: 150px;
    transform: translateX(-50%);
    border-radius: 46% 46% 40% 40%;
    background: radial-gradient(ellipse at 50% 42%, #b5b5b5 0%, var(--crest-light) 30%, var(--crest-dark) 65%, var(--card) 85%);
  }
  .back-url {
    position: absolute; left: 0; right: 0; top: 236px; text-align: center;
    color: var(--text-muted); font-size: 13px; letter-spacing: 3px;
  }
</style>
</head>
<body>
<main class="stage">
  <section class="card card-front" aria-label="Card front">
    <div class="logo">
      <span class="logo-square"></span>
      <span class="logo-name">DRV Ventures Inc.</span>
    </div>
    <div class="crest-small" role="img" aria-label="TORVAN brand crest"></div>
    <div class="divider"></div>
    <div class="contact">
      <p class="contact-name">Marisol Depree</p>
      <p class="contact-title">CEO</p>
      <p class="contact-lines">Ground floor<br>Lindell Plaza Suite 2734<br>George Town,Grand Cayman<br>Cayman Islands,KY1-4823<br>drvventuresinc.example</p>
      <p class="contact-row">
        <svg viewBox="0 0 12 12" aria-hidden="true"><rect x="3" y="0.5" width="6" height="11" rx="1" fill="none" stroke="var(--brand-red)" stroke-width="1.4"/><circle cx="6" cy="9.5" r=".8" fill="var(--brand-red)"/></svg>
        1 555 4180736
      </p>
      <p class="contact-row">
        <svg viewBox="0 0 12 12" aria-hidden="true"><rect x="0.5" y="2" width="11" height="8" fill="var(--brand-red)"/><path d="M0.5 2 L6 6.5 L11.5 2" fill="none" stroke="var(--card)" stroke-width="1"/></svg>
        m.depree@drvventuresinc.example
      </p>
      <p class="contact-row">
        <svg viewBox="0 0 12 12" aria-hidden="true"><circle cx="6" cy="6" r="5.3" fill="none" stroke="var(--brand-red)" stroke-width="1.3"/><ellipse cx="6" cy="6" rx="2.3" ry="5.3" fill="none" stroke="var(--brand-red)" stroke-width="1"/><line x1="0.7" y1="6" x2="11.3" y2="6" stroke="var(--brand-red)" stroke-width="1"/></svg>
        drvventuresinc.example
      </p>
    </div>
  </section>

  <section class="card card-back" aria-label="Card back">
    <div class="crest-large" role="img" aria-label="TORVAN brand crest in silver foil"></div>
    <p class="back-url">www.drvventuresinc.example</p>
  </section>
</main>
</body>
</html>
```